Business Cards Design for the electrical wholesaler: clean bold dynamic :)

We need a business card design that would follow our latest brand guidelines. As an electrical wholesaler we want to bring a fresh look and feel into the industry. The design should be clean bold and dynamic. It should come alive with the renewed energy of our green colour. Our grey colour should keep things balanced and complement the notion of maturity and responsibility. We employ Lato as a corporate font however are not bound by this font and we’re open to interpretation here.

Target Market(s)

Electrical contractors

Industry/Entity Type

Business

Contact Information for Business Card

Logo
Name & Surname: Halyna Dorosh
Job Title: Director of Marketing
Email: halya.dorosh@quillmail.example
Cell phone: XXX.XXX.XXXX
Address: 20517 - 87 Ave. Edmonton, AB, Canada. T6K 4N8
Business Phone: 780.555.0184
Website: www.brovix.example

Font styles to use
Other font styles liked:
• Lato

Requirements
Must have
• Logo & website
Nice to have
• Brand elements - some of them you may find in the attached Brand Guidelines (e.g. three lines on the background signifying "W")

```html
<!DOCTYPE html>
<html lang="en">
<head>
<meta charset="utf-8">
<title>Brovix business card</title>
<link rel="stylesheet" href="https://fonts.googleapis.com/css2?family=Work+Sans:wght@400;500;600&display=swap">
<style>
  :root {
    --green: #8cc541;
    --grey: #4a4a4c;
    --white: #ffffff;
    --stage: #161616;
    --dark-a: #1b1b1b;
    --dark-b: #302f2c;
  }
  * { margin: 0; padding: 0; box-sizing: border-box; }
  html, body {
    width: 1200px; height: 897px; overflow: hidden;
    background: var(--stage);
    font-family: "Work Sans", sans-serif;
  }
  .stage { position: relative; width: 1200px; height: 897px; }
  .card {
    position: absolute; left: 303px; width: 595px; height: 338px;
    border-radius: 18px; overflow: hidden;
  }
  .card-front { top: 92px; background: var(--white); }
  .card-back {
    top: 469px;
    background: linear-gradient(160deg, var(--dark-a) 40%, var(--dark-b) 100%);
  }
  .brand-name {
    position: absolute; font-weight: 500; letter-spacing: -0.5px; line-height: 1;
  }
  .front-brand { left: 30px; top: 44px; font-size: 48px; color: var(--grey); }
  .front-brand-dot {
    position: absolute; left: 30px; top: 55px; width: 34px; height: 34px;
    border-radius: 50%; background: var(--green);
  }
  .front-brand.with-dot { left: 74px; }
  .person { position: absolute; right: 34px; top: 36px; text-align: right; }
  .person-name { font-size: 24px; font-weight: 500; color: var(--green); line-height: 1.1; }
  .person-title { font-size: 16px; color: var(--grey); letter-spacing: 0.5px; margin-top: 2px; }
  .accent-tab {
    position: absolute; right: 0; top: 40px; width: 12px; height: 38px;
    background: var(--green); border-radius: 6px 0 0 6px;
  }
  .contact-band {
    position: absolute; left: 0; top: 200px; width: 345px; height: 114px;
    background: var(--green); border-radius: 0 57px 57px 0;
  }
  .contact-list {
    position: absolute; left: 30px; top: 208px; color: var(--white);
    font-size: 14px; letter-spacing: 0.4px; list-style: none;
  }
  .contact-list li { display: flex; align-items: center; height: 19px; }
  .contact-list svg { width: 10px; height: 10px; margin-right: 10px; flex: none; }
  .address {
    position: absolute; left: 30px; top: 270px; color: var(--white);
    font-size: 14px; letter-spacing: 0.4px; line-height: 17px; font-style: normal;
  }
  .big-brand {
    position: absolute; right: 30px; top: 220px; font-size: 76px;
    font-weight: 600; color: var(--green); line-height: 1; letter-spacing: -1px;
  }
  .back-lockup {
    position: absolute; left: 0; right: 0; top: 126px;
    display: flex; align-items: center; justify-content: center; gap: 18px;
  }
  .back-dot { width: 62px; height: 62px; border-radius: 50%; background: var(--green); }
  .back-brand { position: static; font-size: 74px; color: var(--white); }
</style>
</head>
<body>
<main class="stage">
  <section class="card card-front" aria-label="Card front">
    <span class="front-brand-dot"></span>
    <span class="brand-name front-brand with-dot">brovix</span>

    <div class="person">
      <p class="person-name">Halyna Dorosh</p>
      <p class="person-title">Founder</p>
    </div>
    <span class="accent-tab"></span>

    <div class="contact-band"></div>
    <ul class="contact-list">
      <li>
        <svg viewBox="0 0 10 10" fill="none" stroke="#fff" stroke-width="1.2"><path d="M2 1 L3.5 1 L4.2 3 L3.2 3.8 Q4.5 6 6.2 6.8 L7 5.8 L9 6.5 L9 8 Q5 9 2.5 5.5 Q1 3 2 1 Z"/></svg>
        780.555.0184
      </li>
      <li>
        <svg viewBox="0 0 10 10" fill="none" stroke="#fff" stroke-width="1.1"><rect x="1" y="2.2" width="8" height="5.6"/><path d="M1 2.4 L5 5.4 L9 2.4"/></svg>
        halya.dorosh@quillmail.example
      </li>
      <li>
        <svg viewBox="0 0 10 10" fill="none" stroke="#fff" stroke-width="0.9"><circle cx="5" cy="5" r="4"/><ellipse cx="5" cy="5" rx="1.8" ry="4"/><path d="M1 5 H9 M1.6 3 H8.4 M1.6 7 H8.4"/></svg>
        www.brovix.example
      </li>
    </ul>
    <address class="address">20517 - 87 Ave.<br>Edmonton, AB, Canada. T6K 4N8</address>

    <span class="brand-name big-brand">brovix</span>
  </section>

  <section class="card card-back" aria-label="Card back">
    <div class="back-lockup">
      <span class="back-dot"></span>
      <span class="brand-name back-brand">brovix</span>
    </div>
  </section>
</main>
</body>
</html>
```